Specialised investor in e-mobility and energy wants business card design

We need a business card design that fits our existing corporate design. <The look and feel must be 'sharp'/'clean', dynamic, communicate momentum, professionalism etc (as one would imagine from a firm in the financial sector). We like the idea of a reverse-side of the card that includes the logo, and the name and contact details on the other. We expect the deliverable to be whatever format might be required to be able to get cards printed directly by a service such as kelmo press. Our website is www.zub.capital

```html
<!DOCTYPE html>
<html lang="en">
<head>
<meta charset="utf-8">
<title>Zub Holdings – Business Card</title>
<link href="https://fonts.googleapis.com/css2?family=Montserrat:wght@400;800&display=swap" rel="stylesheet">
<style>
  :root {
    --stage: #1f1f1f;
    --forest: #344f25;
    --leaf: #7ab648;
    --paper: #ffffff;
    --ink: #333333;
  }
  * { margin: 0; padding: 0; box-sizing: border-box; }
  html, body {
    width: 1200px; height: 988px; overflow: hidden;
    background: var(--stage);
    font-family: "Montserrat", Arial, sans-serif;
  }
  .card {
    position: absolute;
    width: 700px; height: 400px;
    border-radius: 22px;
    overflow: hidden;
  }
  .card--front {
    left: 60px; top: 60px;
    background: var(--forest);
    display: flex; align-items: center; justify-content: center;
  }
  .card--back {
    left: 440px; top: 528px;
    background: var(--paper);
  }
  .brand {
    display: flex; align-items: center; gap: 16px;
    font-weight: 800;
    white-space: nowrap;
  }
  .brand__mark {
    width: 20px; height: 20px; border-radius: 50%; flex: none;
  }
  .card--front .brand { color: var(--paper); font-size: 60px; }
  .card--front .brand__mark { background: var(--paper); }
  .card--back .brand {
    position: absolute; left: 44px; top: 178px;
    color: var(--forest); font-size: 30px; gap: 10px;
  }
  .card--back .brand__mark { background: var(--forest); width: 12px; height: 12px; }
  .divider {
    position: absolute; left: 346px; top: 70px;
    width: 1.5px; height: 260px;
    background: var(--forest);
  }
  .contact {
    position: absolute; left: 378px; top: 74px;
    color: var(--ink); font-size: 15px; line-height: 1.45;
  }
  .contact__name {
    font-size: 28px; font-weight: 800; line-height: 1.1;
    color: var(--forest);
  }
  .contact__name span { color: var(--leaf); }
  .contact__role { margin-bottom: 14px; }
  .contact__address { margin-bottom: 14px; }
  .contact__line { display: flex; align-items: center; gap: 10px; }
  .contact__line svg { width: 14px; height: 14px; flex: none; }
</style>
</head>
<body>
  <section class="card card--front">
    <div class="brand"><span class="brand__mark"></span>Zub Holdings</div>
  </section>

  <section class="card card--back">
    <div class="brand"><span class="brand__mark"></span>Zub Holdings</div>
    <div class="divider"></div>
    <div class="contact">
      <p class="contact__name">Marten <span>Ossery</span></p>
      <p class="contact__role">Director/Founder</p>
      <p class="contact__address">1234 Street Name<br>Country Name AB 5748</p>
      <p class="contact__line">
        <svg viewBox="0 0 16 16"><path fill="#7ab648" d="M3.5 1.5l2.5 2.5-1.5 2a9 9 0 0 0 5.5 5.5l2-1.5 2.5 2.5-1.5 2C7 16 0 9 1.5 3z"/></svg>
        123-480-2917
      </p>
      <p class="contact__line">
        <svg viewBox="0 0 16 16"><rect x="1" y="3" width="14" height="10" fill="#7ab648"/><path d="M1 3l7 6 7-6" fill="none" stroke="#fff" stroke-width="1.3"/></svg>
        info@zub.capital
      </p>
      <p class="contact__line">
        <svg viewBox="0 0 16 16"><circle cx="8" cy="8" r="7" fill="#7ab648"/><path d="M1 8h14M8 1c-3 4-3 10 0 14M8 1c3 4 3 10 0 14" fill="none" stroke="#fff" stroke-width="1"/></svg>
        www.zub.capital
      </p>
    </div>
  </section>
</body>
</html>
```